Brookmere Osteopathy flyer

I want a clean clear DL flyer (but also want an A4 poster) promoting a new Osteopathic business in a semi rural area in Tasmania (Australia).
It can have pictures like the examples attached to show people what Osteopathy is (its like Chiropractic and physiotherapy).
I am the sole practioner and am male, so any pictures would be best to be a white male if possible.
I've attached some wording, you can use all, or none of it
I don't have a phone number for the business yet
info@brookmereosteopathy.example
www.brookmereosteopathy.example
Target Market(s)
Australians, from tradies, professionals, babies to retired people
Industry/Entity Type
Health
Look and feel

```html
<!DOCTYPE html>
<html lang="en">
<head>
<meta charset="utf-8">
<title>Brookmere Osteopathy Flyer</title>
<link rel="stylesheet" href="https://fonts.googleapis.com/css2?family=Bebas+Neue&family=Montserrat:ital,wght@0,500;0,600;0,700;0,800;1,800&display=swap">
<style>
  :root {
    --stage: #444444;
    --paper: #f7f8fa;
    --orange: #f0964a;
    --blue: #1d97d2;
    --ink: #111418;
    --photo-light: #dfe4ea;
    --photo-mid: #9aa8b6;
  }
  * { box-sizing: border-box; margin: 0; padding: 0; }
  html, body { width: 897px; height: 1200px; overflow: hidden; background: var(--stage); }
  .flyer {
    position: absolute; left: 23px; top: 0;
    width: 851px; height: 1200px;
    background: var(--paper);
    overflow: hidden;
    font-family: "Montserrat", sans-serif;
    color: var(--ink);
  }
  .brand-seal {
    position: absolute; left: 56px; top: 61px;
    width: 234px; height: 234px;
    border: 2px solid var(--blue); border-radius: 50%;
    display: flex; align-items: center; justify-content: center;
    text-align: center;
  }
  .brand-seal__name {
    font-size: 17px; font-weight: 700; color: var(--blue);
    letter-spacing: 1px; line-height: 1.35; text-transform: uppercase;
  }
  .title {
    position: absolute; left: 62px; top: 336px;
    font-family: "Bebas Neue", sans-serif;
    font-size: 116px; line-height: 87px; letter-spacing: -1px;
  }
  .title__top { color: var(--orange); display: block; }
  .title__bottom { color: var(--blue); display: block; }
  .photo {
    position: absolute; border-radius: 50%; border-style: solid;
  }
  .photo--head {
    left: 402px; top: -113px; width: 468px; height: 468px;
    border-width: 14px; border-color: var(--blue);
    background: linear-gradient(140deg, var(--photo-light), #c9b2a3 55%, #2a3340);
  }
  .photo--shoulder {
    left: 561px; top: 235px; width: 400px; height: 400px;
    border-width: 14px; border-color: var(--orange);
    background: linear-gradient(160deg, #eceff2, #c9a593 45%, #bcd3ea 75%);
  }
  .photo--infant {
    left: 586px; top: 661px; width: 204px; height: 204px;
    border-width: 9px; border-color: var(--blue);
    background: linear-gradient(170deg, #d8d4dc, #e6c8b8 40%, #4aa5cf 75%);
  }
  .photo--abdomen {
    left: 586px; top: 829px; width: 204px; height: 204px;
    border-width: 9px; border-color: var(--blue);
    background: linear-gradient(180deg, #f2f2f2, #dcb7a4 50%, #f4f4f4);
  }
  .reasons__heading {
    position: absolute; left: 60px; top: 578px;
    font-size: 32px; font-weight: 800; font-style: italic;
    color: var(--orange); line-height: 39px; letter-spacing: -0.8px;
  }
  .reasons__list {
    position: absolute; left: 59px; top: 673px;
    list-style: none;
  }
  .reasons__item {
    display: flex; align-items: center; gap: 8px;
    font-size: 18px; font-weight: 500; line-height: 26.1px;
  }
  .reasons__item svg { flex: none; }
  .about {
    position: absolute; left: 60px; top: 968px; width: 430px;
    font-size: 13.6px; font-weight: 600; line-height: 18px;
  }
  .call { position: absolute; left: 60px; top: 1096px; }
  .call__label { font-size: 20px; font-weight: 800; letter-spacing: -0.5px; }
  .call__number {
    font-size: 37px; font-weight: 800; color: var(--orange);
    letter-spacing: 1.5px; line-height: 40px;
  }
  .contact {
    position: absolute; right: 58px; top: 1089px;
    list-style: none; text-align: right;
  }
  .contact__item {
    display: flex; justify-content: flex-end; align-items: center; gap: 6px;
    font-size: 15px; font-weight: 500; line-height: 20.4px;
  }
</style>
</head>
<body>
<main class="flyer">
  <div class="brand-seal">
    <span class="brand-seal__name">Brookmere<br>Osteopathy<br>&amp; Dry Needling</span>
  </div>

  <h1 class="title">
    <span class="title__top">Brookmere</span>
    <span class="title__bottom">Osteopathy</span>
  </h1>

  <div class="photo photo--head" role="img" aria-label="Practitioner treating a patient's head and neck on a treatment table"></div>
  <div class="photo photo--shoulder" role="img" aria-label="Practitioner stretching a patient's shoulder and arm"></div>
  <div class="photo photo--infant" role="img" aria-label="Gentle cranial treatment of a sleeping baby"></div>
  <div class="photo photo--abdomen" role="img" aria-label="Hands working on a patient's lower back"></div>

  <h2 class="reasons__heading">Common Reasons<br>People Visit An Osteopath:</h2>
  <ul class="reasons__list">
    <li class="reasons__item"><svg width="16" height="16" viewBox="0 0 16 16"><circle cx="8" cy="8" r="6.5" fill="none" stroke="var(--blue)" stroke-width="1.6" stroke-dasharray="33 8"/><path d="M4.5 8l2.6 2.6L14 3.5" fill="none" stroke="var(--blue)" stroke-width="2" stroke-linecap="round"/></svg>Back / neck pain</li>
    <li class="reasons__item"><svg width="16" height="16" viewBox="0 0 16 16"><circle cx="8" cy="8" r="6.5" fill="none" stroke="var(--blue)" stroke-width="1.6" stroke-dasharray="33 8"/><path d="M4.5 8l2.6 2.6L14 3.5" fill="none" stroke="var(--blue)" stroke-width="2" stroke-linecap="round"/></svg>Headaches / migraines</li>
    <li class="reasons__item"><svg width="16" height="16" viewBox="0 0 16 16"><circle cx="8" cy="8" r="6.5" fill="none" stroke="var(--blue)" stroke-width="1.6" stroke-dasharray="33 8"/><path d="M4.5 8l2.6 2.6L14 3.5" fill="none" stroke="var(--blue)" stroke-width="2" stroke-linecap="round"/></svg>Joint and muscle pain</li>
    <li class="reasons__item"><svg width="16" height="16" viewBox="0 0 16 16"><circle cx="8" cy="8" r="6.5" fill="none" stroke="var(--blue)" stroke-width="1.6" stroke-dasharray="33 8"/><path d="M4.5 8l2.6 2.6L14 3.5" fill="none" stroke="var(--blue)" stroke-width="2" stroke-linecap="round"/></svg>Pregnancy-related discomfort</li>
    <li class="reasons__item"><svg width="16" height="16" viewBox="0 0 16 16"><circle cx="8" cy="8" r="6.5" fill="none" stroke="var(--blue)" stroke-width="1.6" stroke-dasharray="33 8"/><path d="M4.5 8l2.6 2.6L14 3.5" fill="none" stroke="var(--blue)" stroke-width="2" stroke-linecap="round"/></svg>Disc related issues</li>
    <li class="reasons__item"><svg width="16" height="16" viewBox="0 0 16 16"><circle cx="8" cy="8" r="6.5" fill="none" stroke="var(--blue)" stroke-width="1.6" stroke-dasharray="33 8"/><path d="M4.5 8l2.6 2.6L14 3.5" fill="none" stroke="var(--blue)" stroke-width="2" stroke-linecap="round"/></svg>Sciatica</li>
    <li class="reasons__item"><svg width="16" height="16" viewBox="0 0 16 16"><circle cx="8" cy="8" r="6.5" fill="none" stroke="var(--blue)" stroke-width="1.6" stroke-dasharray="33 8"/><path d="M4.5 8l2.6 2.6L14 3.5" fill="none" stroke="var(--blue)" stroke-width="2" stroke-linecap="round"/></svg>Plantar fasciitis</li>
    <li class="reasons__item"><svg width="16" height="16" viewBox="0 0 16 16"><circle cx="8" cy="8" r="6.5" fill="none" stroke="var(--blue)" stroke-width="1.6" stroke-dasharray="33 8"/><path d="M4.5 8l2.6 2.6L14 3.5" fill="none" stroke="var(--blue)" stroke-width="2" stroke-linecap="round"/></svg>Tendonitis / Bursitis</li>
    <li class="reasons__item"><svg width="16" height="16" viewBox="0 0 16 16"><circle cx="8" cy="8" r="6.5" fill="none" stroke="var(--blue)" stroke-width="1.6" stroke-dasharray="33 8"/><path d="M4.5 8l2.6 2.6L14 3.5" fill="none" stroke="var(--blue)" stroke-width="2" stroke-linecap="round"/></svg>Adhesive capsulitis (frozen shoulder)</li>
    <li class="reasons__item"><svg width="16" height="16" viewBox="0 0 16 16"><circle cx="8" cy="8" r="6.5" fill="none" stroke="var(--blue)" stroke-width="1.6" stroke-dasharray="33 8"/><path d="M4.5 8l2.6 2.6L14 3.5" fill="none" stroke="var(--blue)" stroke-width="2" stroke-linecap="round"/></svg>Tennis / Golfers elbow</li>
  </ul>

  <p class="about">Osteopaths use a combination of joint manipulation, targeted deep tissue massage and stretching to improve function, relieve pain and support the body’s ability to heal itself.</p>

  <div class="call">
    <p class="call__label">CALL US NOW!</p>
    <p class="call__number">555-014-2290</p>
  </div>

  <ul class="contact">
    <li class="contact__item">48 Millbrook Lane, Brookmere
      <svg width="13" height="14" viewBox="0 0 13 14"><path d="M6.5 13s4.5-4.5 4.5-7.5a4.5 4.5 0 0 0-9 0C2 8.5 6.5 13 6.5 13z" fill="none" stroke="var(--orange)" stroke-width="1"/><circle cx="6.5" cy="5.5" r="1.6" fill="none" stroke="var(--orange)" stroke-width="1"/></svg></li>
    <li class="contact__item">www.brookmereosteopathy.example
      <svg width="13" height="13" viewBox="0 0 13 13"><circle cx="6.5" cy="6.5" r="5.5" fill="none" stroke="var(--orange)" stroke-width="1"/><ellipse cx="6.5" cy="6.5" rx="2.4" ry="5.5" fill="none" stroke="var(--orange)" stroke-width="1"/><path d="M1 6.5h11" stroke="var(--orange)" stroke-width="1"/></svg></li>
    <li class="contact__item">info@brookmereosteopathy.example
      <svg width="13" height="11" viewBox="0 0 13 11"><rect x="0.5" y="1" width="12" height="9" fill="none" stroke="var(--orange)" stroke-width="1"/><path d="M0.5 1.5l6 4.5 6-4.5" fill="none" stroke="var(--orange)" stroke-width="1"/></svg></li>
  </ul>
</main>
</body>
</html>
```